Im open to ideas.. I was thinking on my business cards aswell as my logo. a place for my name. email. phone number and abn..

ive attched a file with my business logo. which i dont love the colours.. i was think a dark background with charcoal letters so something along those colour schumes but im open to ideas..

BRM Constructions

```html
<!DOCTYPE html>
<html lang="en">
<head>
<meta charset="utf-8">
<title>BRM Constructions – Business Cards</title>
<link rel="stylesheet" href="https://fonts.googleapis.com/css2?family=Open+Sans:wght@400;600;700&display=swap">
<style>
  :root {
    --backdrop: #3b3430;
    --card: #0f0f10;
    --card-edge: #1b1b1c;
    --silver: #c9c9c9;
    --silver-soft: #b4b4b4;
    --white: #f2f2f2;
    --icon: #d0d0d0;
  }
  * { margin: 0; padding: 0; box-sizing: border-box; }
  html, body {
    width: 1200px;
    height: 844px;
    overflow: hidden;
    background: var(--backdrop);
    font-family: "Open Sans", Arial, sans-serif;
  }
  .stage {
    width: 1200px;
    height: 844px;
    display: flex;
    align-items: center;
    justify-content: center;
    gap: 40px;
  }
  .card {
    position: relative;
    width: 520px;
    height: 300px;
    background: var(--card);
    border: 1px solid var(--card-edge);
    box-shadow: 0 10px 26px rgba(0,0,0,0.45);
  }
  .brand {
    position: absolute;
    left: 0;
    right: 0;
    text-align: center;
    color: var(--silver);
    font-weight: 700;
    line-height: 1;
  }
  .brand-name {
    display: block;
    font-size: 58px;
    letter-spacing: 2px;
  }
  .brand-line {
    display: block;
    margin-top: 8px;
    font-size: 13px;
    letter-spacing: 9px;
    padding-left: 9px;
  }
  .card-front .brand { top: 62px; }
  .card-back .brand { top: 104px; }

  .person {
    position: absolute;
    left: 48px;
    top: 200px;
    text-align: right;
    width: 160px;
  }
  .person-name {
    color: var(--silver);
    font-size: 19px;
    font-weight: 600;
    line-height: 1.2;
  }
  .person-role {
    color: var(--silver-soft);
    font-size: 13px;
    line-height: 1.5;
  }
  .person-abn {
    color: var(--silver-soft);
    font-size: 13px;
    line-height: 1.6;
  }
  .person-abn strong {
    color: var(--white);
    font-weight: 700;
  }
  .contact {
    position: absolute;
    left: 272px;
    top: 196px;
    list-style: none;
  }
  .contact li {
    display: flex;
    align-items: center;
    gap: 8px;
    color: var(--white);
    font-size: 13px;
    line-height: 22px;
  }
  .contact svg {
    width: 11px;
    height: 11px;
    fill: var(--icon);
    flex: none;
  }
</style>
</head>
<body>
<main class="stage">
  <section class="card card-front" aria-label="Business card front">
    <div class="brand">
      <span class="brand-name">BRM</span>
      <span class="brand-line">CONSTRUCTIONS</span>
    </div>
    <div class="person">
      <p class="person-name">Daniel Harper</p>
      <p class="person-role">Managing Director</p>
      <p class="person-abn">ABN NO: <strong>67890</strong></p>
    </div>
    <ul class="contact">
      <li>
        <svg viewBox="0 0 16 16" aria-hidden="true"><path d="M3.6 1.2l2.3 2.6c.4.4.4 1 0 1.4L4.7 6.4c.9 2 2.8 3.9 4.9 4.9l1.2-1.2c.4-.4 1-.4 1.4 0l2.6 2.3c.4.4.4 1 0 1.4l-1.3 1.3c-.6.6-1.5.8-2.3.5C6.5 14 2 9.5.4 4.8c-.3-.8-.1-1.7.5-2.3L2.2 1.2c.4-.4 1-.4 1.4 0z"/></svg>
        <span>(045)-318-2264</span>
      </li>
      <li>
        <svg viewBox="0 0 16 16" aria-hidden="true"><path d="M0 3h16v1.2L8 9 0 4.2z"/><path d="M0 5.6l8 4.8 8-4.8V13H0z"/></svg>
        <span>info@brmbuild.com</span>
      </li>
      <li>
        <svg viewBox="0 0 16 16" aria-hidden="true"><circle cx="8" cy="8" r="7.5"/></svg>
        <span>www.brmbuild.com</span>
      </li>
    </ul>
  </section>

  <section class="card card-back" aria-label="Business card back">
    <div class="brand">
      <span class="brand-name">BRM</span>
      <span class="brand-line">CONSTRUCTIONS</span>
    </div>
  </section>
</main>
</body>
</html>
```